Tallowmere Riding School Flyer Design

We need a flyer for our Horse riding school, called Tallowmere Riding School.

At Tallowmere Riding School, Horses and ponies are carefully matched to suit each rider's experience, ability and confidence. I am a Qualified instructor, equipped to train all levels from nervous beginners to the more advanced.

Horse riding is fun! Riders, particularly children, are taught not only skills on the horse, but skills that are integral to good horsemanship and ownership of horses.

We regularly host Ladies Days, Guest Instructors, 1 hour Trail Rides and Pony Ride Days!

We teach people how to interact safely with, and care for horses so they develop a genuine love and respect for the animals and the sport.

In addition to fundamental riding techniques including walk, trot, and canter, we teach our students:
Grooming and Care of horses, Safety around horses, Balance and Co-Ordination, How to saddle up and care for Tack, Responsibility for equipment and horse, Confidence and Confidence Building for all Ages.

Private and group lessons start at 5 years of age upwards.

We recommend children 4 years and under partake in 15 minute pony rides, mainly due to their attention span!

Industry/Entity Type

School

```html
<!DOCTYPE html>
<html lang="en">
<head>
<meta charset="utf-8">
<title>Tallowmere Riding School Flyer</title>
<link href="https://fonts.googleapis.com/css2?family=Arimo:wght@400;700&family=Roboto:wght@400;500&family=Delius&display=swap" rel="stylesheet">
<style>
  :root {
    --page-bg: #ececec;
    --panel-green: #434d40;
    --panel-dark: #2f332c;
    --accent-lime: #c8dc2a;
    --wave-lime: #b5cf2a;
    --text-light: #ffffff;
    --sky-top: #6f9fd6;
    --sky-mid: #dfe9f4;
    --grass-top: #79b13b;
    --grass-bottom: #3f7a22;
  }
  html, body {
    margin: 0;
    width: 1200px;
    height: 1000px;
    overflow: hidden;
    background: var(--page-bg);
  }
  .flyer {
    position: absolute;
    left: 97px;
    top: 133px;
    width: 1018px;
    height: 722px;
    overflow: hidden;
    background: var(--panel-dark);
  }
  .hero-photo {
    position: absolute;
    inset: 0 0 auto 0;
    height: 440px;
    background: linear-gradient(180deg, var(--sky-top) 0%, #a9c6e8 30%, var(--sky-mid) 58%, var(--grass-top) 74%, var(--grass-bottom) 100%);
  }
  .flyer-shapes {
    position: absolute;
    inset: 0;
  }
  .brand {
    position: absolute;
    left: 0;
    width: 378px;
    text-align: center;
    color: var(--text-light);
  }
  .brand-mark {
    position: absolute;
    left: 123px;
    top: 368px;
    width: 126px;
    height: 126px;
    border: 2px solid var(--text-light);
    border-radius: 50%;
    box-sizing: border-box;
  }
  .brand-name {
    top: 533px;
    margin: 0;
    font: 400 34px/1 "Roboto", sans-serif;
    letter-spacing: 6px;
  }
  .brand-sub {
    top: 582px;
    margin: 0;
    font: 500 17px/1 "Roboto", sans-serif;
    letter-spacing: 3.5px;
  }
  .brand-location {
    top: 620px;
    margin: 0;
    font: 400 18px/1.2 "Delius", cursive;
    color: var(--accent-lime);
    letter-spacing: 0.5px;
  }
  .brand-phone {
    top: 660px;
    margin: 0;
    font: 700 34px/1 "Arimo", sans-serif;
    letter-spacing: 6px;
  }
  .about {
    position: absolute;
    left: 405px;
    top: 450px;
    width: 593px;
    color: var(--text-light);
    font: 400 18.5px/24px "Arimo", sans-serif;
  }
  .about p {
    margin: 0 0 10px;
    text-align: justify;
  }
  .about .school-name {
    color: var(--accent-lime);
  }
  .about .services {
    text-align: left;
    white-space: nowrap;
    font-size: 18px;
  }
</style>
</head>
<body>
  <main class="flyer">
    <div class="hero-photo" role="img" aria-label="Two chestnut horses galloping across a grassy meadow dotted with yellow dandelions under a blue cloudy sky"></div>

    <svg class="flyer-shapes" width="1018" height="722" viewBox="0 0 1018 722" aria-hidden="true">
      <path class="dark-band" d="M240 372 C 450 398 610 440 750 428 C 880 418 960 400 1018 385 L1018 722 L240 722 Z" fill="var(--panel-dark)"/>
      <path class="lime-wave" d="M240 372 C 450 398 610 440 750 428 C 880 418 960 400 1018 385" fill="none" stroke="var(--wave-lime)" stroke-width="4"/>
      <path class="brand-panel" d="M0 268 C 200 248 372 400 378 722 L0 722 Z" fill="var(--panel-green)"/>
      <path class="brand-panel-edge" d="M0 268 C 200 248 372 400 378 722" fill="none" stroke="var(--text-light)" stroke-width="3"/>
    </svg>

    <div class="brand-mark" aria-hidden="true"></div>
    <h1 class="brand brand-name">TALLOWMERE</h1>
    <h2 class="brand brand-sub">RIDING SCHOOL</h2>
    <p class="brand brand-location">Find us at Brackenvale Rd, Hollowmere</p>
    <p class="brand brand-phone">0400 555 018</p>

    <section class="about">
      <p><span class="school-name">At Tallowmere Riding School,</span> Horses and ponies are carefully matched to suit each rider's experience, ability and confidence. I am a Qualified instructor, tutoring from nervous beginners to the more advanced.</p>
      <p>I teach people how to interact safely with, and care for horses as so to develop a genuine love and respect for the animals and the sport.</p>
      <p>Private, group lessons and trail rides available, All ages catered for!</p>
      <p class="services">Ask about Ladies Days, Guest Instructors, Trail Rides and Pony Rides</p>
    </section>
  </main>
</body>
</html>
```